Brookvale Building Company - advertisement poster

I am looking to print some canvas signs to advertise my general contracting company, Brookvale Building Company. The sign will measure 6' long x 3' high so the size should match that ratio. I already have a logo icon, which is the Letter 'B' and some trees that I would like to incorporate, see attached. I would also like the to have the following information listed:
1) phone number: 831-555-0172
2) email: brookvalebuildingcompany@mailnest.example
3) website: brookvalebuildingcompany.example
4) Lic#4826130
5) I want to use this text: "BUILD WITH THE B-CREW!"

The ad should be relatively simple and clean. Black and Green are my company colors. I am open to creative ideas!

Target Market(s)

People looking to renovate their homes

Industry/Entity Type

Construction

Colors
59FF00
82FF00
B8FF75
E3FFCB
F4FFEA

Requirements
Must have
• Must have my company logo
Should not have
• No photos or complex graphics

```html
<!DOCTYPE html>
<html lang="en">
<head>
<meta charset="utf-8">
<title>Brookvale Building Company – Canvas Sign</title>
<link href="https://fonts.googleapis.com/css2?family=Bebas+Neue&family=Montserrat:ital,wght@0,700;0,800;1,700;1,800&display=swap" rel="stylesheet">
<style>
  :root {
    --green: #66b03a;
    --green-dark: #437a26;
    --black: #000000;
    --white: #ffffff;
    --backdrop: #d4d4d4;
  }
  * { margin: 0; padding: 0; box-sizing: border-box; }
  html, body { width: 1200px; height: 713px; overflow: hidden; background: var(--backdrop); }
  .sign {
    position: absolute; left: 20px; top: 61px;
    width: 1160px; height: 590px;
    background: var(--white); overflow: hidden;
    font-family: 'Montserrat', sans-serif;
  }
  .sign > * { position: absolute; }

  /* Brand panel */
  .brand-frame { left: 42px; top: 0; width: 358px; height: 278px; background: var(--green); }
  .brand-panel {
    left: 47px; top: 31px; width: 347px; height: 241px; background: var(--black);
    display: flex; flex-direction: column; align-items: center; justify-content: center;
    color: var(--white); font-weight: 800; text-align: center; padding-bottom: 24px;
  }
  .brand-est { font-size: 10px; letter-spacing: 4px; margin-bottom: 14px; }
  .brand-name { font-size: 34px; letter-spacing: 1px; line-height: 1; }
  .brand-sub { font-size: 13px; letter-spacing: 5px; margin-top: 10px; }
  .brand-rule { width: 106px; height: 2px; background: var(--green); margin-top: 12px; }
  .licence-tag {
    left: 101px; top: 260px; width: 240px; height: 38px; background: var(--green);
    font-family: 'Bebas Neue', sans-serif; font-size: 30px; line-height: 40px;
    text-align: center; color: var(--black);
  }

  /* House headline */
  .house { left: 0; top: 0; width: 1160px; height: 340px; }
  .hammer { left: 719px; top: 58px; width: 100px; height: 52px; background: var(--black); border-radius: 10px 26px 6px 10px; }
  .headline { font-family: 'Bebas Neue', sans-serif; line-height: 0.82; }
  .headline-build { left: 626px; top: 128px; font-size: 122px; color: var(--white); }
  .headline-with { left: 845px; top: 131px; font-size: 60px; color: var(--black); line-height: 0.73; }
  .headline-crew { left: 640px; top: 226px; font-size: 118px; color: var(--black); letter-spacing: 1px; }

  /* Contact band */
  .band { left: 0; top: 330px; width: 1160px; height: 260px; background: var(--black); border-top: 5px solid var(--green); }
  .contact-arrow { left: 47px; top: 348px; width: 440px; height: 145px; }
  .contact-label {
    left: 80px; top: 399px; font-size: 40px; font-weight: 800;
    color: var(--black); letter-spacing: -0.5px;
  }
  .phone-badge { left: 517px; top: 373px; width: 104px; height: 104px; }
  .phone-number {
    left: 648px; top: 378px; font-size: 70px; font-weight: 800; font-style: italic;
    color: var(--white); letter-spacing: -1px;
  }
  .link-row { display: flex; align-items: center; gap: 18px; }
  .link-icon { width: 44px; height: 44px; flex: none; }
  .link-text {
    color: var(--white); font-weight: 700; font-style: italic; font-size: 15.5px;
    border-bottom: 2px solid var(--green); padding-bottom: 3px; letter-spacing: 0.3px;
  }
  .link-web { left: 90px; top: 505px; }
  .link-mail { left: 561px; top: 505px; }
</style>
</head>
<body>
<main class="sign">
  <svg class="house" viewBox="0 0 1160 340" aria-hidden="true">
    <rect x="0" y="330" width="1160" height="10" fill="var(--black)"/>
    <polygon points="456,152 764,25 1028,152 1028,335 532,335 532,152" fill="var(--green)"/>
    <polygon points="764,25 780,25 1103,152 1088,152" fill="var(--green-dark)"/>
    <polygon points="456,152 780,25 1088,152" fill="var(--green)"/>
    <polygon points="764,35 780,25 1103,152 1072,152" fill="var(--green-dark)"/>
    <rect x="1001" y="152" width="27" height="183" fill="var(--green-dark)"/>
  </svg>

  <div class="brand-frame"></div>
  <div class="brand-panel">
    <div class="brand-est">ESTD 2020</div>
    <div class="brand-name">BROOKVALE</div>
    <div class="brand-sub">BUILDING COMPANY</div>
    <div class="brand-rule"></div>
  </div>
  <div class="licence-tag">LICENCED - 4826130</div>

  <div class="hammer" role="img" aria-label="Hammer illustration"></div>
  <div class="headline headline-build">BUILD</div>
  <div class="headline headline-with">WITH<br>THE</div>
  <div class="headline headline-crew">B-CREW!</div>

  <div class="band"></div>
  <svg class="contact-arrow" viewBox="0 0 440 145" aria-hidden="true">
    <polygon points="384,0 440,72 384,145 384,127 366,127 402,72 366,18 384,18" fill="var(--green-dark)"/>
    <polygon points="0,18 366,18 402,72 366,127 0,127" fill="var(--green)"/>
  </svg>
  <div class="contact-label">CONTACT US</div>

  <svg class="phone-badge" viewBox="0 0 104 104" aria-hidden="true">
    <circle cx="52" cy="52" r="49" fill="var(--black)" stroke="var(--green)" stroke-width="4"/>
    <path d="M32 30 c4-4 8-3 10 0 l5 9 c1 3 0 5-2 7 l-3 2 c3 7 8 12 15 15 l2-3 c2-2 4-3 7-2 l9 5 c3 2 4 6 0 10 c-5 5-13 6-22 1 c-10-6-19-15-24-26 c-4-9-2-15 3-18z" fill="var(--white)"/>
    <g fill="none" stroke="var(--white)" stroke-width="3.5" stroke-linecap="round">
      <path d="M56 40 a8 8 0 0 1 8 8"/>
      <path d="M56 31 a17 17 0 0 1 17 17"/>
      <path d="M56 22 a26 26 0 0 1 26 26"/>
    </g>
  </svg>
  <div class="phone-number">831-555-0172</div>

  <div class="link-row link-web">
    <svg class="link-icon" viewBox="0 0 44 44" aria-hidden="true">
      <circle cx="22" cy="22" r="20" fill="var(--black)" stroke="var(--green)" stroke-width="3"/>
      <g fill="none" stroke="var(--white)" stroke-width="1.4">
        <circle cx="21" cy="21" r="10"/>
        <ellipse cx="21" cy="21" rx="4.5" ry="10"/>
        <path d="M11 21 h20 M13 15.5 h16 M13 26.5 h16"/>
      </g>
      <path d="M25 23 l9 4 -4 1.5 3 4 -2 1.5 -3-4 -2.5 3z" fill="var(--white)" stroke="var(--black)" stroke-width="0.8"/>
    </svg>
    <span class="link-text">BROOKVALEBUILDINGCOMPANY.EXAMPLE</span>
  </div>

  <div class="link-row link-mail">
    <svg class="link-icon" viewBox="0 0 44 44" aria-hidden="true">
      <circle cx="22" cy="22" r="20" fill="var(--black)" stroke="var(--green)" stroke-width="3"/>
      <circle cx="22" cy="22" r="11" fill="var(--white)"/>
      <rect x="16" y="18" width="12" height="8" fill="none" stroke="var(--black)" stroke-width="1.3"/>
      <path d="M16 18 l6 5 6-5 M16 26 l4.5-4 M28 26 l-4.5-4" fill="none" stroke="var(--black)" stroke-width="1.1"/>
    </svg>
    <span class="link-text">BROOKVALEBUILDINGCOMPANY@MAILNEST.EXAMPLE</span>
  </div>
</main>
</body>
</html>
```